Medical Billing Company Needs a Business Card Design

We need a business card design for a Florida based medical billing company called 'Clinicians Keystone Solutions'. We specialize in providing revenue cycle management services to physician and therapist offices (we're basically their back-office processing partner for providing billing software, claims submissions, A/R follow-up and patient statements & collections. Our logo is red and blue-ish, so make sure that whatever other elements are used will match appropriately. Our current business card design has a too small font size. I'd like to project an image that shows we are modern & reliable. On a side note, I'm planning on using ZUB for printing these cards.

Target Market(s)

Office managers, physicians, therapists

Industry/Entity Type

Printing

Requirements
Must have
• Logo
Name of Employee
Phone
Fax
E-mail
Website

```html
<!DOCTYPE html>
<html lang="en">
<head>
<meta charset="utf-8">
<title>Clinicians Keystone Solutions – Business Card</title>
<link href="https://fonts.googleapis.com/css2?family=Cabin:wght@400;500;600&display=swap" rel="stylesheet">
<style>
  :root {
    --navy: #2c2c7c;
    --navy-deep: #232368;
    --red: #c0262d;
    --white: #ffffff;
    --metal-light: #eef0f1;
    --metal-mid: #d9dcdf;
    --metal-dark: #c4c8cc;
    --ink-grey: #4a4d52;
    --page: #e9e6e1;
  }
  * { margin: 0; padding: 0; box-sizing: border-box; }
  html, body { width: 1200px; height: 720px; overflow: hidden; }
  body {
    background: var(--page);
    font-family: "Cabin", "Gill Sans", sans-serif;
    position: relative;
  }
  .card {
    position: absolute;
    top: 200px;
    width: 560px;
    height: 320px;
    border-radius: 4px;
    overflow: hidden;
    background:
      repeating-linear-gradient(0deg, rgba(255,255,255,0.18) 0 1px, rgba(0,0,0,0.025) 1px 2px, transparent 2px 3px),
      linear-gradient(115deg, var(--metal-mid) 0%, var(--metal-light) 35%, var(--metal-dark) 60%, var(--metal-light) 85%, var(--metal-mid) 100%);
    box-shadow: 0 8px 18px rgba(0,0,0,0.18);
  }
  .card--front { left: 30px; }
  .card--back { left: 610px; }

  .card__band {
    position: absolute;
    top: 0; right: 0; bottom: 0;
    width: 275px;
    background: linear-gradient(160deg, var(--navy) 0%, var(--navy-deep) 100%);
  }

  .brand {
    position: absolute;
    top: 40px;
    left: 40px;
    display: flex;
    align-items: center;
    gap: 10px;
  }
  .brand__name {
    color: var(--navy);
    font-size: 22px;
    font-weight: 500;
    letter-spacing: 2px;
  }
  .brand__mark {
    width: 12px; height: 12px;
    background: var(--red);
  }

  .person { position: absolute; left: 40px; top: 170px; }
  .person__name { color: var(--navy); font-size: 21px; font-weight: 500; }
  .person__title { color: var(--red); font-size: 15px; margin-top: 2px; }

  .contact {
    position: absolute;
    right: 20px;
    top: 100px;
    list-style: none;
    color: var(--white);
    font-size: 14px;
    text-align: right;
    line-height: 22px;
  }
  .contact li { display: flex; justify-content: flex-end; align-items: center; gap: 6px; }
  .contact svg { width: 12px; height: 12px; fill: var(--white); }
  .contact .contact__gap { margin-top: 12px; }
  .contact .contact__address { margin-top: 10px; font-size: 13px; }

  .back-brand {
    position: absolute;
    left: 0; right: 0; top: 122px;
    display: flex; justify-content: center; align-items: center; gap: 12px;
  }
  .back-brand__name {
    color: var(--navy);
    font-size: 30px;
    font-weight: 500;
    letter-spacing: 3px;
  }
  .back-brand__mark { width: 16px; height: 16px; background: var(--red); }

  .back-web {
    position: absolute;
    left: 0; right: 0; bottom: 40px;
    text-align: center;
    font-size: 19px;
    letter-spacing: 1px;
    color: var(--ink-grey);
  }
  .back-web__first { color: var(--navy); }
  .back-web__second { color: var(--red); }
</style>
</head>
<body>

<section class="card card--front" aria-label="Business card front">
  <div class="card__band" role="img" aria-label="Decorative navy swoosh with red and white stripes"></div>

  <div class="brand">
    <span class="brand__name">CLINICIANS KEYSTONE</span>
    <span class="brand__mark"></span>
  </div>

  <div class="person">
    <p class="person__name">Your Name</p>
    <p class="person__title">Title</p>
  </div>

  <ul class="contact">
    <li>
      <svg viewBox="0 0 12 12" aria-hidden="true"><circle cx="6" cy="6" r="6"/><path d="M3.5 3h1.5l.6 1.6-.9.7a4 4 0 0 0 2 2l.7-.9 1.6.6V8.5a1 1 0 0 1-1 1A5.5 5.5 0 0 1 2.5 4a1 1 0 0 1 1-1z" fill="var(--navy)"/></svg>
      123-456-0789
    </li>
    <li>
      <svg viewBox="0 0 12 12" aria-hidden="true"><rect x="3" y="1" width="6" height="4"/><rect x="1" y="5" width="10" height="6" rx="1"/></svg>
      123-456-0789
    </li>
    <li>www.cliniciankeystone.com</li>
    <li class="contact__gap">
      <svg viewBox="0 0 12 12" aria-hidden="true"><rect x="1" y="2.5" width="10" height="7" rx="1"/><path d="M1.5 3l4.5 3.5L10.5 3" fill="none" stroke="var(--navy)" stroke-width="1"/></svg>
      info@cliniciankeystone.com
    </li>
    <li>
      <svg viewBox="0 0 12 12" aria-hidden="true"><circle cx="6" cy="6" r="6"/><path d="M0.5 6h11M6 0.5c-3 3-3 8 0 11M6 0.5c3 3 3 8 0 11" fill="none" stroke="var(--navy)" stroke-width="0.8"/></svg>
      www.cliniciankeystone.com
    </li>
    <li class="contact__address">Street Name, City Name, State Zip Code</li>
  </ul>
</section>

<section class="card card--back" aria-label="Business card back">
  <div class="back-brand">
    <span class="back-brand__name">CLINICIANS KEYSTONE</span>
    <span class="back-brand__mark"></span>
  </div>
  <p class="back-web">www.<span class="back-web__first">clinician</span><span class="back-web__second">keystone</span>.com</p>
</section>

</body>
</html>
```